Project Overview:
We are looking to create a website for a monthly subscription IPTV service in WordPress. The website should provide a seamless user experience for customers to sign up for the service and manage their account information. We need the following pages: Home Page, Product Page, Sign-Up Page, and Account Information Page.

Home Page:
The Home Page design should be simple and clean, with a dark theme and minimalistic design elements. We would like to include graphics of popular movie shows displayed on multiple devices. The page should highlight the key benefits and features of our service and provide a clear call-to-action for visitors to sign up.

Product Page:
The Product Page should provide detailed information about our subscription tiers and pricing plans. It should highlight the key features of each plan and provide a clear comparison between them. The page should also include a call-to-action button for visitors to sign up.

Sign-Up Page:
The Sign-Up Page is the conversion page where members will sign up for the service. It should collect the following information: Name, Phone Number, Email, Password, and Payment Information. The design should be simple, intuitive, and easy to use. It should highlight the benefits of our service and provide a clear call-to-action for visitors to sign up.

Account Information Page:
The Account Information Page should allow members to view and manage their account details. It should include the following information: Profile Image, Contact Details, Password Management, Payment Information Management, and Membership Expiration Date. The design should be user-friendly, intuitive, and easy to navigate.

Goals: The primary goal of the website is to provide an easy-to-use portal for customers to sign up for the service and manage their account information. The website should be user-friendly and visually appealing to attract potential customers.

Scope: The scope of the project includes designing a home page, a sign-up page, an account information page, and a payment information page. The website should be designed to be responsive and accessible on desktop and mobile devices.

Design Preferences: The design should be clean, modern, and visually appealing. The use of a color palette that is consistent with the brand identity is recommended. The website should be easy to navigate and provide a clear call-to-action for users to sign up for the service.

FYI: The subscription service I am designing a website for is related to an IPTV service. IPTV stands for Internet Protocol Television, which is a digital television broadcasting protocol that uses the internet to deliver TV programs and videos to viewers. The website will allow customers to sign up for the IPTV service and access their account information such as user name and password, membership tier, name, and payment details. Please let me know if you have any further questions, and I would be happy to provide more details. Thank you!

Dear Designers,

Thank you for your participation in our project. After reviewing the designs received so far, we have decided to update the brief to better reflect our needs and preferences. We apologize for any confusion this may cause, but we believe that these changes will result in better design submissions and a more successful project overall.

The updated brief is as follows:

We are looking to create a website for WordPress.

Also, here is the updated Brief.

Project Title: WordPress Website Design for Monthly Subscription IPTV Service

Project Overview:
We are looking to create a website for a monthly subscription IPTV service. The website should provide a seamless user experience for customers to sign up for the service and manage their account information. We need the following pages: Home Page, Product Page, Sign-Up Page, and Account Information Page.

Home Page:

Product Page:

Sign-Up Page:

Account Information Page:

Design Preferences:
We prefer a dark theme with minimalistic design elements and hits of our logo colors. The website should be easy to use and navigate, with clear calls-to-action and simple, intuitive forms. The design should be optimized for mobile devices and load quickly.

We hope that these updates provide you with a clearer understanding of our requirements and preferences. Please let us know if you have any questions or concerns. We look forward to seeing your revised designs.

Thank you again for your participation.
We will guarantee this project as soon as we see something we like that meets the updated requirements.

The website's target audience is individuals who are interested in subscribing to the monthly service.

4 page

• One item for sale and a client profile section.

```html
<!DOCTYPE html>
<html lang="en">
<head>
<meta charset="utf-8">
<title>STREAMVO – IPTV Subscription</title>
<link href="https://fonts.googleapis.com/css2?family=Roboto:wght@400;500;700&family=Varela+Round&display=swap" rel="stylesheet">
<style>
:root{
  --red:#ee1111;
  --black:#000;
  --dark:#120d0a;
  --white:#fff;
  --text:#222;
  --muted:#555;
  --teal-top:#07d1bd;
  --teal-bottom:#006a78;
  --grey-num:#d8d8d8;
  --line:#8a8a8a;
}
*{box-sizing:border-box;margin:0;padding:0}
html,body{width:1200px;height:3734px;overflow:hidden}
body{position:relative;background:var(--white);font-family:"Varela Round",sans-serif;color:var(--text)}
.abs{position:absolute}
.head{font-family:"Roboto",sans-serif;font-weight:500;text-transform:uppercase;color:var(--text)}
.center{text-align:center}

/* Hero */
.hero-bg{left:0;top:0;width:1200px;height:672px;background:radial-gradient(ellipse at 75% 40%,#1d3b55 0%,#0c1a27 45%,#04080d 100%)}
.topbar{left:16px;top:0;width:1184px;height:122px;background:rgba(0,0,0,.55)}
.brand{left:51px;top:46px;font-family:"Roboto",sans-serif;font-weight:700;font-size:34px;color:var(--red);letter-spacing:1px}
.nav{top:70px;font-family:"Roboto",sans-serif;font-size:16px;color:var(--white)}
.nav.active{color:var(--red)}
.signup-top{left:983px;top:19px;width:104px;height:32px;border:1px solid #bbb;border-radius:3px;color:var(--white);font-family:"Roboto",sans-serif;font-size:14px;display:flex;align-items:center;justify-content:center}
.hero-title{left:0;width:1200px;top:188px;font-size:60px;line-height:72px;color:var(--white);font-weight:500}
.hero-text{left:320px;width:560px;top:342px;font-size:22px;line-height:41px;color:var(--white)}
.arrow-circle{width:46px;height:46px;border:2px solid var(--white);border-radius:50%}
.btn{display:flex;align-items:center;background:var(--red);color:var(--white);border-radius:26px;font-family:"Roboto",sans-serif;font-size:16px;text-transform:uppercase}
.btn .plus{width:32px;height:32px;border-radius:50%;background:var(--white);margin-left:auto;margin-right:8px;display:flex;align-items:center;justify-content:center}
.btn span.lbl{padding-left:32px}

/* Feature cards */
.feature{width:304px;height:288px;top:610px;background:var(--white);box-shadow:0 2px 8px rgba(0,0,0,.25)}
.feature .icon{position:absolute;left:124px;top:20px}
.feature .num{position:absolute;left:218px;top:8px;font-family:"Roboto",sans-serif;font-weight:700;font-size:58px;color:var(--grey-num)}
.feature h3{position:absolute;top:88px;width:100%;font-size:23px}
.feature p{position:absolute;left:32px;right:30px;top:132px;font-size:15px;line-height:31px;color:var(--muted)}
.feature .more{position:absolute;top:245px;width:100%;font-family:"Roboto",sans-serif;font-size:14px;font-weight:500;color:var(--text)}
.feature .more b{color:var(--red);margin-right:8px}

/* Stream */
.stream-bg{left:0;top:953px;width:1200px;height:380px;background:var(--black)}
.stream-photo{left:0;top:953px;width:1200px;height:380px}
.stream-title{left:0;width:702px;top:982px;font-size:29px;color:var(--white)}
.stream-text{left:131px;width:442px;top:1037px;font-size:18px;line-height:31px;color:var(--white)}

/* Plans */
.plans-title{left:0;width:1200px;top:1394px;font-size:28px}
.plan{width:308px;height:435px;top:1485px;border-radius:18px;overflow:hidden;background:var(--white);box-shadow:0 2px 10px rgba(0,0,0,.18)}
.plan svg.band{position:absolute;left:0;top:0}
.plan h3{position:absolute;top:28px;width:100%;font-size:28px;color:#111}
.plan .icon{position:absolute;left:128px;top:128px}
.plan p{position:absolute;left:20px;right:20px;top:204px;font-size:17px;line-height:30px;color:#0b4a4a;text-align:center}
.plan .price{position:absolute;top:268px;width:100%;text-align:center;font-family:"Roboto",sans-serif;color:var(--white);font-size:34px;font-weight:700}
.plan .price small{font-size:18px;font-weight:500}
.plan .btn{position:absolute;left:55px;top:339px;width:198px;height:48px}
.plan .btn span.lbl{padding-left:28px}

/* Subscribe */
.sub-photo{left:0;top:2002px;width:1200px;height:415px;background:linear-gradient(100deg,#2b1a12 0%,#6b3e22 35%,#3a2a24 60%,#3b4a66 80%,#6a5a4a 100%)}
.sub-box{left:552px;top:2069px;width:493px;height:232px;background:rgba(200,200,200,.55)}
.sub-title{left:552px;width:493px;top:2100px;font-size:29px;line-height:41px;color:#111}
.sub-input{left:616px;top:2207px;width:213px;height:48px;background:var(--white);border-radius:24px 0 0 24px;font-size:15px;color:#444;display:flex;align-items:center;padding-left:26px}
.sub-btn{left:829px;top:2207px;width:144px;height:48px;background:var(--red);border-radius:0 24px 24px 0;color:var(--white);font-family:"Roboto",sans-serif;font-size:16px;display:flex;align-items:center;justify-content:center}

/* Testimonials */
.testi-title{left:0;width:1184px;top:2452px;font-size:28px}
.testi{width:299px;height:294px;top:2546px;background:var(--white);box-shadow:0 2px 9px rgba(0,0,0,.25);overflow:hidden}
.testi svg.band{position:absolute;left:0;top:0}
.testi .avatar{position:absolute;left:34px;top:25px;width:58px;height:58px;border-radius:50%;background:linear-gradient(#c9c2bb,#8a7f77);border:2px solid var(--white)}
.testi h4{position:absolute;left:110px;top:40px;font-size:19px;color:#111}
.testi p{position:absolute;left:28px;right:28px;top:100px;font-size:17.5px;line-height:31px;text-align:center;color:#333}

/* Contact */
.contact-title{left:0;width:1184px;top:2878px;font-size:28px}
.form-box{left:94px;top:2934px;width:500px;height:312px;background:var(--white);box-shadow:0 2px 10px rgba(0,0,0,.25)}
.field{left:132px;width:421px;height:29px;border:1px solid #999;font-size:13px;color:#444;display:flex;align-items:center;padding-left:14px}
.form-btn{left:300px;top:3196px;width:77px;height:29px;background:var(--red);color:var(--white);font-size:13px;border-radius:3px;display:flex;align-items:center;justify-content:center}
.map{left:594px;top:2934px;width:503px;height:312px;background:linear-gradient(135deg,#eef0e6,#dfe6d3 50%,#e8ece1)}

/* Footer */
.footer{left:0;top:3293px;width:1200px;height:441px;background:radial-gradient(ellipse at 30% 50%,#2c1f15,#120c08 70%)}
.f-brand{left:112px;top:3350px;font-family:"Roboto",sans-serif;font-weight:700;font-size:32px;color:var(--red)}
.f-about{left:112px;width:298px;top:3414px;font-size:18px;line-height:31px;color:var(--white)}
.f-head{top:3350px;font-family:"Roboto",sans-serif;font-weight:500;font-size:18px;color:var(--white)}
.f-link{font-size:17.5px;color:var(--white)}
.social{top:3597px;width:18px;height:18px;border-radius:50%;border:2px solid var(--white)}
.f-email{left:875px;top:3427px;width:212px;height:42px;border:1px solid #ccc;font-family:"Roboto",sans-serif;font-size:12px;color:var(--white);display:flex;align-items:center;padding-left:9px}
.f-email-btn{left:1050px;top:3427px;width:37px;height:42px;border:1px solid #ccc;display:flex;align-items:center;justify-content:center}
.f-rule{left:112px;top:3650px;width:975px;height:1px;background:#6a5a44}
.copy{left:0;width:1184px;top:3680px;font-size:18px;color:var(--white)}
</style>
</head>
<body>

<!-- Hero -->
<div class="abs hero-bg" role="img" aria-label="Dark room with a person watching a glowing computer monitor"></div>
<header class="abs topbar"></header>
<div class="abs brand">STREAMVO</div>
<div class="abs nav active" style="left:399px">HOME</div>
<div class="abs nav" style="left:511px">ABOUT US</div>
<div class="abs nav" style="left:657px">SERVICES</div>
<div class="abs nav" style="left:801px">TESTIMONIALS</div>
<div class="abs nav" style="left:985px">CONTACT US</div>
<div class="abs signup-top">SIGN UP</div>

<h1 class="abs head center hero-title">New way for your<br>entertainment</h1>
<p class="abs hero-text">Lorem ipsum dolor sit amet, consectetur adipiscing elit, sed do eiusmod tempor incididunt ut labore et dolore magna aliqua. Ut enim ad minim veniam</p>
<div class="abs btn" style="left:484px;top:500px;width:198px;height:50px"><span class="lbl">Learn more</span><span class="plus"><svg width="14" height="14" viewBox="0 0 14 14"><path d="M7 1v12M1 7h12" stroke="#e11" stroke-width="3"/></svg></span></div>

<div class="abs arrow-circle" style="left:26px;top:318px"><svg width="42" height="42" viewBox="0 0 42 42"><path d="M24 12l-9 9 9 9" fill="none" stroke="#fff" stroke-width="2.5"/></svg></div>
<div class="abs arrow-circle" style="left:1126px;top:318px"><svg width="42" height="42" viewBox="0 0 42 42"><path d="M18 12l9 9-9 9" fill="none" stroke="#fff" stroke-width="2.5"/></svg></div>

<!-- Feature cards -->
<div class="abs feature" style="left:110px">
  <svg class="icon" width="54" height="48" viewBox="0 0 54 48" fill="none" stroke="#e22" stroke-width="2.4"><rect x="3" y="12" width="48" height="32" rx="4"/><rect x="8" y="17" width="38" height="22" rx="2"/><path d="M19 3l8 9 8-9"/></svg>
  <div class="num">01</div>
  <h3 class="head center">TV &amp; Streaming</h3>
  <p>Lorem ipsum dolor sit amet, consectetur adipiscing elit, sed do eiusmod tempor incididunt</p>
  <div class="more center"><b>+</b>LEARN MORE</div>
</div>
<div class="abs feature" style="left:448px">
  <svg class="icon" width="54" height="50" viewBox="0 0 54 50" fill="none" stroke="#e22" stroke-width="2.4"><rect x="6" y="3" width="26" height="44" rx="3"/><path d="M12 12h14M12 18h14M12 24h8"/><path d="M30 26v-6a3 3 0 016 0v10l6-2a4 4 0 014 5l-4 12H32l-6-9"/></svg>
  <div class="num">02</div>
  <h3 class="head center">All for mobile</h3>
  <p>Lorem ipsum dolor sit amet, consectetur adipiscing elit, sed do eiusmod tempor incididunt</p>
  <div class="more center"><b>+</b>LEARN MORE</div>
</div>
<div class="abs feature" style="left:784px">
  <svg class="icon" width="54" height="50" viewBox="0 0 54 50" fill="none" stroke="#e22" stroke-width="2.4"><circle cx="27" cy="25" r="21"/><ellipse cx="27" cy="25" rx="9" ry="21"/><path d="M6 25h42M10 14h34M10 36h34"/></svg>
  <div class="num">03</div>
  <h3 class="head center">Service</h3>
  <p>Lorem ipsum dolor sit amet, consectetur adipiscing elit, sed do eiusmod tempor incididunt</p>
  <div class="more center"><b>+</b>LEARN MORE</div>
</div>

<!-- More to stream -->
<div class="abs stream-bg"></div>
<svg class="abs stream-photo" width="1200" height="380" viewBox="0 0 1200 380" role="img" aria-label="Woman on a sofa watching a wall of shows on a television">
  <defs><linearGradient id="room" x1="0" y1="0" x2="1" y2="1"><stop offset="0" stop-color="#6a5540"/><stop offset=".5" stop-color="#3e3026"/><stop offset="1" stop-color="#1f1813"/></linearGradient></defs>
  <polygon points="671,0 1200,0 1200,380 601,380" fill="url(#room)"/>
  <polygon points="667,0 671,0 601,380 597,380" fill="#e11"/>
</svg>
<h2 class="abs head center stream-title">More to stream</h2>
<p class="abs center stream-text">Sed ut perspiciatis unde omnis iste natus error sit voluptatem accusantium doloremque laudantium, totam rem aperiam, eaque ipsa quae ab illo inventore veritatis et quasi architecto beatae vitae dicta sunt explicabo. Nemo enim ipsam voluptatem quia voluptas quuntur magni dolores</p>
<div class="abs btn" style="left:251px;top:1253px;width:198px;height:48px"><span class="lbl">Learn more</span><span class="plus"><svg width="14" height="14" viewBox="0 0 14 14"><path d="M7 1v12M1 7h12" stroke="#e11" stroke-width="3"/></svg></span></div>

<!-- Plans -->
<h2 class="abs head center plans-title">Choose your plan</h2>

<svg width="0" height="0" style="position:absolute"><defs><linearGradient id="teal" x1="0" y1="0" x2="0" y2="1"><stop offset="0" stop-color="#07d1bd"/><stop offset="1" stop-color="#006a78"/></linearGradient></defs></svg>

<div class="abs plan" style="left:112px">
  <svg class="band" width="308" height="435" viewBox="0 0 308 435"><polygon points="0,119 154,87 308,119 308,435 0,435" fill="url(#teal)"/></svg>
  <h3 class="head center">Basic</h3>
  <svg class="icon" width="52" height="52" viewBox="0 0 52 52" fill="none" stroke="#fff" stroke-width="2.4"><rect x="16" y="4" width="32" height="32" rx="3"/><path d="M12 14H6v32h32v-6"/><rect x="9" y="12" width="30" height="30" rx="3"/></svg>
  <p>Lorem ipsum dolor sit amet, consectetur adipiscing elit,</p>
  <div class="price">$12<small>per month</small></div>
  <div class="btn"><span class="lbl">Choose plan</span><span class="plus"><svg width="14" height="14" viewBox="0 0 14 14"><path d="M7 1v12M1 7h12" stroke="#e11" stroke-width="3"/></svg></span></div>
</div>
<div class="abs plan" style="left:445px">
  <svg class="band" width="308" height="435" viewBox="0 0 308 435"><polygon points="0,119 154,87 308,119 308,435 0,435" fill="url(#teal)"/></svg>
  <h3 class="head center">Standard</h3>
  <svg class="icon" width="52" height="56" viewBox="0 0 52 56" fill="none" stroke="#fff" stroke-width="2.2"><path d="M34 48H8V4h24l8 8v22"/><path d="M14 16h18M14 23h18M14 30h18M14 37h10"/><circle cx="38" cy="44" r="8"/><path d="M34 44l3 3 5-6"/></svg>
  <p>Lorem ipsum dolor sit amet, consectetur adipiscing elit,</p>
  <div class="price">$22<small>per month</small></div>
  <div class="btn"><span class="lbl">Choose plan</span><span class="plus"><svg width="14" height="14" viewBox="0 0 14 14"><path d="M7 1v12M1 7h12" stroke="#e11" stroke-width="3"/></svg></span></div>
</div>
<div class="abs plan" style="left:778px">
  <svg class="band" width="308" height="435" viewBox="0 0 308 435"><polygon points="0,119 154,87 308,119 308,435 0,435" fill="url(#teal)"/></svg>
  <h3 class="head center">Premium</h3>
  <svg class="icon" width="56" height="56" viewBox="0 0 56 56" fill="none" stroke="#fff" stroke-width="2.4" stroke-linejoin="round"><path d="M28 4l7 16 17 1-13 11 4 17-15-9-15 9 4-17L4 21l17-1z"/></svg>
  <p>Lorem ipsum dolor sit amet, consectetur adipiscing elit,</p>
  <div class="price">$42<small>per month</small></div>
  <div class="btn"><span class="lbl">Choose plan</span><span class="plus"><svg width="14" height="14" viewBox="0 0 14 14"><path d="M7 1v12M1 7h12" stroke="#e11" stroke-width="3"/></svg></span></div>
</div>

<!-- Subscribe -->
<div class="abs sub-photo" role="img" aria-label="Family sitting together watching a projected movie in a warmly lit room"></div>
<div class="abs sub-box"></div>
<h2 class="abs head center sub-title">Subscribe here to get<br>exclusive news &amp; offer</h2>
<div class="abs sub-input">YOUR EMAIL ID</div>
<div class="abs sub-btn">CONTACT US</div>

<!-- Testimonials -->
<h2 class="abs head center testi-title">Testimonials</h2>
<svg class="abs" style="left:34px;top:2683px" width="28" height="18" viewBox="0 0 28 18"><path d="M26 9H3M10 2L3 9l7 7" fill="none" stroke="#111" stroke-width="2.6"/></svg>
<svg class="abs" style="left:1137px;top:2683px" width="28" height="18" viewBox="0 0 28 18"><path d="M2 9h23M18 2l7 7-7 7" fill="none" stroke="#111" stroke-width="2.6"/></svg>

<div class="abs testi" style="left:110px">
  <svg class="band" width="299" height="60" viewBox="0 0 299 60"><polygon points="0,0 299,0 299,4 0,58" fill="#e11"/></svg>
  <div class="avatar" role="img" aria-label="Customer portrait"></div>
  <h4 class="head">Lorem ipsum</h4>
  <p>Sed ut perspiciatis unde omnis iste natus error sit voluptatem accusantium doloremque laudantium, totam rem aperiam, eaque</p>
</div>
<div class="abs testi" style="left:451px">
  <svg class="band" width="299" height="60" viewBox="0 0 299 60"><polygon points="0,0 299,0 299,4 0,58" fill="#e11"/></svg>
  <div class="avatar" role="img" aria-label="Customer portrait"></div>
  <h4 class="head">Lorem ipsum</h4>
  <p>Sed ut perspiciatis unde omnis iste natus error sit voluptatem accusantium doloremque laudantium, totam rem aperiam, eaque</p>
</div>
<div class="abs testi" style="left:788px">
  <svg class="band" width="299" height="60" viewBox="0 0 299 60"><polygon points="0,0 299,0 299,4 0,58" fill="#e11"/></svg>
  <div class="avatar" role="img" aria-label="Customer portrait"></div>
  <h4 class="head">Lorem ipsum</h4>
  <p>Sed ut perspiciatis unde omnis iste natus error sit voluptatem accusantium doloremque laudantium, totam rem aperiam, eaque</p>
</div>

<!-- Get in touch -->
<h2 class="abs head center contact-title">Get in touch</h2>
<div class="abs form-box"></div>
<div class="abs field" style="top:2959px">User Name</div>
<div class="abs field" style="top:3018px">Password</div>
<div class="abs field" style="top:3078px">Membership tier</div>
<div class="abs field" style="top:3140px">Payment Details</div>
<div class="abs form-btn">SIGN UP</div>
<div class="abs map" role="img" aria-label="Street map showing the office location"></div>

<!-- Footer -->
<footer class="abs footer"></footer>
<div class="abs f-brand">STREAMVO</div>
<p class="abs f-about">Lorem ipsum dolor sit amet, consectetur adipiscing elit, sed do eiusmod tempor incididunt ut labore et dolore magna aliqua. Ut enim ad minim veon ullamco</p>
<div class="abs social" style="left:108px"></div>
<div class="abs social" style="left:143px"></div>
<div class="abs social" style="left:186px"></div>

<div class="abs f-head" style="left:445px">USEFUL LINKS</div>
<div class="abs f-link" style="left:446px;top:3418px">Area Coverage</div>
<div class="abs f-link" style="left:446px;top:3459px">How We Deliver</div>
<div class="abs f-link" style="left:446px;top:3500px">Customer Support</div>
<div class="abs f-link" style="left:446px;top:3541px">Careers</div>

<div class="abs f-head" style="left:654px">GET IN TOUCH</div>
<svg class="abs" style="left:654px;top:3420px" width="14" height="18" viewBox="0 0 14 18"><path d="M7 17s6-6 6-10A6 6 0 001 7c0 4 6 10 6 10z" fill="none" stroke="#fff" stroke-width="1.3"/><circle cx="7" cy="7" r="2" fill="none" stroke="#fff" stroke-width="1.3"/></svg>
<div class="abs f-link" style="left:678px;top:3417px;line-height:31px;width:170px">Lorem ipsum dolor sit amet</div>
<svg class="abs" style="left:654px;top:3490px" width="14" height="14" viewBox="0 0 14 14"><path d="M3 1l3 3-2 2c1 2 2 3 4 4l2-2 3 3-2 2C6 13 1 8 1 3z" fill="none" stroke="#fff" stroke-width="1.2"/></svg>
<div class="abs f-link" style="left:678px;top:3486px">+1 555 014 2290</div>
<svg class="abs" style="left:654px;top:3538px" width="16" height="12" viewBox="0 0 16 12"><rect x="1" y="1" width="14" height="10" fill="none" stroke="#fff" stroke-width="1.2"/><path d="M1 1l7 6 7-6" fill="none" stroke="#fff" stroke-width="1.2"/></svg>
<div class="abs f-link" style="left:678px;top:3533px">hello@streamvo.com</div>

<div class="abs f-head" style="left:875px">SUBSCRIBE</div>
<div class="abs f-email">Email address</div>
<div class="abs f-email-btn"><svg width="12" height="10" viewBox="0 0 12 10"><path d="M1 5h9M7 2l3 3-3 3" fill="none" stroke="#fff" stroke-width="1.3"/></svg></div>

<div class="abs f-rule"></div>
<p class="abs center copy">Copyrights © 2023 STREAMVO. All Rights Reserved.</p>

</body>
</html>
```